Coastal Learner Bureau business cards

Australian company about to start offering its services. We recruit international students to come to study English, vocational education and postgraduate courses in Australia. We help them find the institution and select the right city they want to come to Australia. We are a young, online oriented and supportive agency. Our clients are between 18 and 35 years old, mainly University students, young professionals or people with work experience. We provide much more information that any other agency offer. We administrate a Facebook group with more than 11.000 members that daily ask questions about general information when coming to Australia, while they are here and even after they leave the country

Target Market(s)

International students from South America, Central America and Europe

Industry/Entity Type

Student

Contact Information for Business Card

Tomas Bilbrea
Managing Director
tomas@kelvarin.com.au
www.kelvoria.com.au
+61 491058264
Melbourne, Australia

Font styles to use
Serif
Sans Serif

Colors

Designer to choose colors to be used in the design.

Requirements
Must have
• Horizontal design
• Standard business card size and shape. If font uses green or yellow colours, they will have to match the ones from the logo
Nice to have
• UPDATE: Use the contents of the green image to design one of the card sides. Use our logo in the background of that side as watermark.
• Passport image, or immigration stamps. A picture of the Yarra River (from Melbourne) would be cool as well.
Should not have
• Non-standard business card size and shape
• Not black as the background colour of any sides as we are not a VIP agency or a hight class service. We are orientes to young people and they like colours, pictures, something attractive.
• Vertical design
• NO YELLOW or BLACK AS THE BACKGROUND COLOUR OF ANY SIDE OF THE BIZ CARD

```html
<!DOCTYPE html>
<html lang="en">
<head>
<meta charset="utf-8">
<title>Coastal Learner Bureau business cards</title>
<link href="https://fonts.googleapis.com/css2?family=Open+Sans:wght@400;600&family=Tinos:wght@700&display=swap" rel="stylesheet">
<style>
  :root {
    --stage: #888888;
    --card-white: #ffffff;
    --brand-green: #135e3d;
    --brand-yellow: #e6bb15;
    --ink: #1d1d1b;
    --tagline: #ffffff;
  }
  * { margin: 0; padding: 0; box-sizing: border-box; }
  html, body {
    width: 1200px; height: 900px; overflow: hidden;
    background: var(--stage);
    font-family: "Open Sans", Arial, sans-serif;
  }
  .canvas { position: relative; width: 1200px; height: 900px; }
  .card {
    position: absolute; top: 306px;
    width: 440px; height: 271px; overflow: hidden;
  }
  .card--front { left: 149px; background: var(--card-white); }
  .card--back { left: 608px; background: var(--brand-green); }

  .corner-tab { position: absolute; left: 0; top: 25px; }

  .holder { position: absolute; left: 41px; top: 27px; }
  .holder__name {
    font-size: 14px; font-weight: 400; letter-spacing: 0.2px;
    color: var(--brand-green); line-height: 18px;
  }
  .holder__name .first { color: var(--brand-yellow); }
  .holder__role { font-size: 11.5px; color: var(--ink); line-height: 18px; }

  .wordmark {
    position: absolute; font-weight: 600; color: var(--brand-green);
    font-size: 40px; letter-spacing: -0.5px; line-height: 1;
    display: flex; align-items: center; gap: 10px;
  }
  .wordmark__dot {
    width: 14px; height: 14px; border-radius: 50%;
    background: var(--brand-yellow);
  }
  .card--front .wordmark { left: 244px; top: 104px; }
  .card--back .wordmark {
    left: 0; right: 0; top: 104px; justify-content: center;
    color: var(--card-white);
  }

  .contacts { position: absolute; left: 23px; top: 184px; list-style: none; }
  .contacts li {
    display: flex; align-items: center; gap: 6px;
    font-size: 12px; color: var(--ink); line-height: 16px;
  }
  .contacts svg { width: 9px; height: 9px; fill: var(--brand-yellow); flex: none; }

  .city {
    position: absolute; right: 24px; top: 216px;
    font-size: 12px; color: var(--ink); line-height: 16px;
  }
  .base-bands { position: absolute; left: 0; bottom: 0; }

  .tagline {
    position: absolute; left: 0; right: 0; top: 226px; text-align: center;
    font-family: "Tinos", "Times New Roman", serif; font-weight: 700;
    font-size: 14px; color: var(--tagline); letter-spacing: 0.3px;
  }
</style>
</head>
<body>
<main class="canvas">
  <section class="card card--front" aria-label="Card front">
    <svg class="corner-tab" width="30" height="38" viewBox="0 0 30 38" aria-hidden="true">
      <rect x="0" y="0" width="13" height="38" fill="var(--brand-green)"/>
      <polygon points="10,0 29,0 29,38 18,38" fill="var(--brand-yellow)"/>
    </svg>
    <div class="holder">
      <p class="holder__name"><span class="first">TOMAS</span> BILBREA</p>
      <p class="holder__role">Managing Director</p>
    </div>
    <div class="wordmark"><span class="wordmark__dot"></span>Kelvoria</div>
    <ul class="contacts">
      <li><svg viewBox="0 0 10 10"><path d="M2 0.5l2 2-1 1.2c.6 1.3 1.6 2.3 2.9 2.9l1.2-1 2 2-1.3 1.9C4.6 9.4.6 5.4.5 2z"/></svg>+61 491058264</li>
      <li><svg viewBox="0 0 10 10"><rect x="0" y="2" width="10" height="6.5"/><path d="M0 2l5 3.5L10 2" stroke="#fff" stroke-width="1" fill="none"/></svg>tomas@kelvarin.com.au</li>
      <li><svg viewBox="0 0 10 10"><circle cx="5" cy="5" r="5"/><path d="M0 5h10M5 0c-2 2.5-2 7.5 0 10M5 0c2 2.5 2 7.5 0 10" stroke="#fff" stroke-width="0.8" fill="none"/></svg>www.kelvoria.com.au</li>
    </ul>
    <p class="city">Melbourne, Australia</p>
    <svg class="base-bands" width="440" height="15" viewBox="0 0 440 15" aria-hidden="true">
      <polygon points="0,1 217,1 207,15 0,15" fill="var(--brand-green)"/>
      <polygon points="222,1 440,1 440,15 209,15" fill="var(--brand-yellow)"/>
    </svg>
  </section>

  <section class="card card--back" aria-label="Card back">
    <div class="wordmark"><span class="wordmark__dot"></span>Kelvoria</div>
    <p class="tagline">HACEMOS MÁS POR TI!</p>
  </section>
</main>
</body>
</html>
```